Media Services Start-up -- Corporate Website and Logo Design. Inspiration required!

We need a logo design and corporate website design, including coding, for our start-up business.
Vennatra’s value proposition is based on bringing together media content from a vast number of geographies globally, adding human and AI curation, translation and editing, and delivering the content using tailored customer interfaces. On the one hand, the business brings together media coverage from all over the world, and on the other it brings together content, human skills and technology to deliver a supreme customer experience.
Vennatra is a B2B media monitoring and analytics business with emphasis on global customers. Vennatra's service offering is centred around sourcing media content from different markets, processing, storing and delivering the content and insights derived from it using an online platform / mobile app.
The messaging we want to create through the logo is:
- Global scope
- Speed of delivery
- Cost-efficiency
- Multi-lingual
- Tailor-made
- Trustworthy
Target Market(s)
Business to business, PR / Communications, Media, Marketing
Logo Text
Vennatra
Coding
Coded - Design and coding required
Number of Pages Required
5+ page
Font styles to use
Other font styles liked:
- See Design Brief for details
Colors
Designer to choose colors to be used in the design.

```html
<!DOCTYPE html>
<html lang="en">
<head>
<meta charset="utf-8">
<title>Vennatra — Delivering Global Media Intelligence</title>
<link rel="stylesheet" href="https://fonts.googleapis.com/css2?family=Roboto:wght@700&family=Roboto+Condensed:wght@700&family=Nunito+Sans:wght@400;600;700&display=swap">
<style>
  :root {
    --teal: #3dae9d;
    --ink: #1e1e1e;
    --nav: #333333;
    --white: #ffffff;
    --line: #cfcfcf;
    --muted: #6b6b6b;
  }
  * { margin: 0; padding: 0; box-sizing: border-box; }
  html, body { width: 1200px; height: 635px; overflow: hidden; }
  body { position: relative; font-family: "Nunito Sans", sans-serif; background: var(--white); }

  .site-header { position: absolute; top: 0; left: 0; width: 1200px; height: 92px; background: var(--white); }
  .brand { position: absolute; left: 141px; top: 11px; display: flex; align-items: center; gap: 12px; }
  .brand-dot { width: 70px; height: 70px; border: 2px solid var(--teal); border-radius: 50%; }
  .brand-name { font-family: "Roboto", sans-serif; font-weight: 700; font-size: 32px; color: var(--ink); }
  .main-nav a { position: absolute; top: 36px; font-size: 14.5px; color: var(--nav); text-decoration: none; }
  .main-nav a.active { color: var(--teal); }
  .sign-in { position: absolute; left: 967px; top: 30px; width: 92px; height: 33px; background: var(--teal); color: var(--white); font-size: 14px; font-weight: 600; display: flex; align-items: center; justify-content: center; }

  .hero { position: absolute; top: 92px; left: 0; width: 1200px; height: 493px; }
  .hero-photo { position: absolute; inset: 0; background: linear-gradient(100deg, #4b5660 0%, #6d6f70 40%, #8a7f7b 60%, #5d6266 100%); }
  .hero-photo::after { content: ""; position: absolute; inset: 0; background: radial-gradient(ellipse at 50% 40%, rgba(190,170,160,.35), transparent 60%); }
  .hero-title { position: absolute; left: 139px; top: 156px; font-family: "Roboto Condensed", sans-serif; font-weight: 700; font-size: 50px; line-height: 51px; color: var(--white); white-space: nowrap; }
  .hero-text { position: absolute; left: 143px; top: 272px; width: 452px; font-size: 15.5px; line-height: 23.3px; color: var(--white); }
  .hero-text .accent { color: var(--teal); }
  .arrow-ornament { position: absolute; left: 599px; top: 144px; width: 156px; height: 62px; background: rgba(255,255,255,.07); border-radius: 30px; }

  .lead-form { position: absolute; left: 755px; top: 108px; width: 304px; height: 292px; background: var(--white); }
  .lead-form h2 { position: absolute; top: 32px; width: 100%; text-align: center; font-family: "Roboto", sans-serif; font-size: 20px; color: var(--ink); }
  .lead-form h2 span { color: var(--teal); }
  .field { position: absolute; left: 29px; width: 247px; height: 35px; border: 1px solid var(--line); display: flex; align-items: center; padding-left: 10px; gap: 8px; font-size: 11px; color: var(--muted); }
  .field svg { width: 15px; height: 15px; }
  .submit { position: absolute; left: 29px; top: 221px; width: 247px; height: 36px; background: var(--teal); color: var(--white); font-size: 15px; font-weight: 600; display: flex; align-items: center; justify-content: center; }

  .site-footer { position: absolute; top: 585px; left: 0; width: 1200px; height: 50px; background: var(--teal); }
  .copyright { position: absolute; left: 141px; top: 17px; font-size: 12px; color: var(--white); }
  .social { position: absolute; top: 11px; width: 28px; height: 28px; border: 1.5px solid var(--white); border-radius: 50%; color: var(--white); font-size: 9px; font-weight: 700; display: flex; align-items: center; justify-content: center; }
</style>
</head>
<body>
<header class="site-header">
  <div class="brand"><span class="brand-dot"></span><span class="brand-name">Vennatra</span></div>
  <nav class="main-nav">
    <a class="active" href="#" style="left:427px">Home</a>
    <a href="#" style="left:501px">Solutions</a>
    <a href="#" style="left:596px">How We Do It</a>
    <a href="#" style="left:721px">Our People</a>
    <a href="#" style="left:830px">Our Technology</a>
  </nav>
  <a class="sign-in">SIGN IN</a>
</header>

<section class="hero">
  <div class="hero-photo" role="img" aria-label="Background photo of hands working at a laptop with overlaid analytics charts"></div>
  <h1 class="hero-title">DELIVERING GLOBAL<br>MEDIA INTELLIGENCE</h1>
  <p class="hero-text"><span class="accent">Vennatra</span> is an international media intelligence service provider. We help communications teams builds and operate truly global media monitoring and measurement programmes.</p>
  <div class="arrow-ornament" role="img" aria-label="Hand-drawn looping arrow pointing to the sign-up form"></div>
  <form class="lead-form">
    <h2>Learn More about <span>Vennatra</span></h2>
    <div class="field" style="top:73px"><svg viewBox="0 0 16 16" fill="none" stroke="#888" stroke-width="1.2"><circle cx="8" cy="5" r="3"/><path d="M2.5 15v-2a5.5 5.5 0 0 1 11 0v2z"/></svg>Name*</div>
    <div class="field" style="top:122px"><svg viewBox="0 0 16 16" fill="none" stroke="#888" stroke-width="1.2"><rect x="1.5" y="3.5" width="13" height="9" rx="1"/><path d="M1.5 4l6.5 5 6.5-5"/></svg>Email*</div>
    <div class="field" style="top:172px"><svg viewBox="0 0 16 16" fill="none" stroke="#888" stroke-width="1.2"><path d="M4 1.5l2.5 3-1.5 2a8 8 0 0 0 4.5 4.5l2-1.5 3 2.5-1.5 2.5C7 14 2 9 1.5 3.5z"/></svg>Phone*</div>
    <div class="submit">GET STARTED</div>
  </form>
</section>

<footer class="site-footer">
  <p class="copyright">© 2019 Vennatra Analytics Media. All rights reserved.</p>
  <span class="social" style="left:925px">Nx</span>
  <span class="social" style="left:960px">Tk</span>
  <span class="social" style="left:996px">Lp</span>
  <span class="social" style="left:1031px">Rs</span>
</footer>
</body>
</html>
```